Book Cover: Quiet Harbor: Small Ceremonies For The Restless Soul

I would like a full cover spread- front, back and spine as well as a stand alone front cover for Kindle for the book. Design a cover that mirrors the profound depth and dynamic energy of 'Quiet Harbor.' Envision a visual tapestry that draws readers into a transformative journey, where spirituality and self-care unite. Explore vibrant colors, intricate textures, and a sense of inner radiance that beckons readers to explore the book's rich wisdom within. See images for design inspiration attached. Even though some of the images are cartoon, I'd like the cover to be more serious than playful and very elegant.

About this book (back cover copy)
Are you ready to embark on a transformative journey and elevate your daily existence? "Quiet Harbor" is a treasure trove of practical yet profound rituals and wisdom from renowned self-care, healing, and spirituality experts.

Within these pages, you'll uncover a tapestry of guidance and insight from some of the world's most respected mentors. Their collective wisdom is your key to creating a sacred sanctuary within your everyday life.

From invigorating morning rituals to meditative practices, empowering affirmations, and transformative energy healing, you'll find a rich tapestry of tools to nurture a deeper connection with yourself and the universe.

Whether you're a seasoned practitioner or a newcomer to the world of self-care and spirituality, "Quiet Harbor" is your trusted companion on the journey to transform your life and elevate your daily experience. Open this book today and start your sacred, fulfilling adventure.

Colors
0094D4
00A9DD
6FCCEA
C7EBF8
E9F6FB
E54698
E96AAD
F1A4CE
F9D9EA
FCEFF6
6B429C
8869AF
B7A5CE
E3DAEB
F3F0F8

Requirements
Must have
• Title: Quiet Harbor: Subtitle: Small Ceremonies For The Restless Soul Name of Publisher: Lantern Bough Publishing- Logo on the back Back cover copy

```html
<!DOCTYPE html>
<html lang="en">
<head>
<meta charset="utf-8">
<title>Quiet Harbor – Full Cover Spread</title>
<link href="https://fonts.googleapis.com/css2?family=Allura&family=Cormorant+Garamond:ital,wght@0,500;0,600;1,500&family=Crimson+Text:ital,wght@0,400;0,700;1,400&family=Arimo:wght@400&display=swap" rel="stylesheet">
<style>
  :root {
    --stage: #1f1f1f;
    --paper: #ffffff;
    --ink: #1a1a1a;
    --rose: #c23a78;
    --gold-light: #f7df86;
    --gold-mid: #d9b24a;
    --gold-deep: #a7802a;
    --bloom-pink: #e54698;
    --bloom-pink-soft: #f1a4ce;
    --bloom-violet: #6b429c;
    --bloom-lilac: #b7a5ce;
    --blush: #fcEff6;
    --placeholder: #ececec;
  }
  * { margin: 0; padding: 0; box-sizing: border-box; }
  html, body {
    width: 1200px; height: 1200px; overflow: hidden;
    background: var(--stage);
  }
  .spread {
    position: absolute; left: 40px; top: 202px;
    width: 1120px; height: 795px;
    background: var(--paper);
  }
  .gold-script {
    font-family: 'Allura', cursive;
    background: linear-gradient(100deg, var(--gold-light) 0%, var(--gold-mid) 45%, var(--gold-deep) 75%, var(--gold-mid) 100%);
    -webkit-background-clip: text; background-clip: text;
    color: transparent;
    line-height: 1;
    white-space: nowrap;
  }
  .subtitle {
    font-family: 'Cormorant Garamond', serif;
    color: var(--rose);
    white-space: nowrap;
  }
  .subtitle em { font-style: italic; font-weight: 500; }
  .subtitle strong { font-style: normal; font-weight: 600; }

  /* Back cover */
  .back-cover { position: absolute; left: 0; top: 0; width: 515px; height: 795px; }
  .back-title { position: absolute; left: 0; top: 40px; width: 515px; height: 160px; }
  .back-title .line-one { position: absolute; left: 150px; top: 0; font-size: 100px; }
  .back-title .line-two { position: absolute; left: 205px; top: 70px; font-size: 72px; }
  .back-cover .subtitle {
    position: absolute; left: 0; top: 193px; width: 515px;
    text-align: center; font-size: 22px;
  }
  .blurb {
    position: absolute; left: 58px; top: 236px; width: 400px;
    font-family: 'Crimson Text', serif; font-size: 13.6px; line-height: 18.4px;
    color: var(--ink); text-align: center;
  }
  .blurb p + p { margin-top: 18.4px; }
  .blurb b { font-weight: 700; }
  .publisher-mark {
    position: absolute; left: 58px; top: 694px;
    font-family: 'Crimson Text', serif; font-weight: 400;
    color: var(--ink); font-size: 21px; line-height: 28px; text-align: center;
  }
  .publisher-mark span { display: block; letter-spacing: 2px; font-size: 17px; }
  .barcode-space {
    position: absolute; left: 333px; top: 674px; width: 138px; height: 83px;
    background: var(--placeholder);
  }

  /* Spine */
  .spine { position: absolute; left: 515px; top: 0; width: 90px; height: 795px; }
  .spine-stack {
    position: absolute; left: 50%; top: 26px; transform: translateX(-50%);
    writing-mode: vertical-rl; display: flex; align-items: center; gap: 12px;
    height: 750px;
  }
  .spine-title { font-size: 52px; }
  .spine .subtitle { font-size: 16px; }
  .spine-publisher {
    font-family: 'Arimo', sans-serif; font-weight: 400; font-size: 15px;
    color: var(--ink); margin-top: 8px; white-space: nowrap;
  }

  /* Front cover */
  .front-cover { position: absolute; left: 605px; top: 0; width: 515px; height: 795px; overflow: hidden; }
  .cover-art {
    position: absolute; left: 60px; top: 80px; width: 455px; height: 680px;
    background:
      radial-gradient(ellipse 38% 22% at 62% 24%, rgba(229,70,152,0.85), rgba(229,70,152,0) 100%),
      radial-gradient(ellipse 22% 14% at 78% 20%, rgba(107,66,156,0.7), rgba(107,66,156,0) 100%),
      radial-gradient(ellipse 18% 12% at 70% 38%, rgba(217,178,74,0.55), rgba(217,178,74,0) 100%),
      radial-gradient(ellipse 45% 40% at 68% 52%, rgba(249,217,234,0.9), rgba(252,239,246,0) 100%),
      radial-gradient(ellipse 30% 45% at 85% 80%, rgba(183,165,206,0.45), rgba(243,240,248,0) 100%);
  }
  .front-cover .subtitle {
    position: absolute; left: 0; top: 36px; width: 515px;
    text-align: center; font-size: 26px;
  }
  .front-title { position: absolute; left: 0; top: 470px; width: 515px; height: 300px; }
  .front-title .line-one { position: absolute; left: 30px; top: 0; font-size: 200px; }
  .front-title .line-two { position: absolute; left: 140px; top: 140px; font-size: 140px; }
</style>
</head>
<body>
<main class="spread">

  <section class="back-cover">
    <h2 class="back-title">
      <span class="gold-script line-one">Quiet</span>
      <span class="gold-script line-two">Harbor</span>
    </h2>
    <p class="subtitle"><em>Small Ceremonies For</em> <strong>The Restless Soul</strong></p>
    <div class="blurb">
      <p><b>Are you ready to embark on a transformative journey and elevate your daily existence?</b> <i>"Quiet Harbor"</i> is a treasure trove of practical yet profound rituals and wisdom from renowned self-care, healing, and spirituality experts.</p>
      <p>Within these pages, you'll uncover a tapestry of guidance and insight from some of the world's most respected mentors. Their collective wisdom is your key to creating a sacred sanctuary within your everyday life.</p>
      <p>From invigorating morning rituals to meditative practices, empowering affirmations, and transformative energy healing, you'll find a rich tapestry of tools to nurture a deeper connection with yourself and the universe.</p>
      <p>Whether you're a seasoned practitioner or a newcomer to the world of self-care and spirituality, "Quiet Harbor" is your trusted companion on the journey to transform your life and elevate your daily experience. Open this book today and start your sacred, fulfilling adventure.</p>
    </div>
    <div class="publisher-mark">Lantern Bough<span>Publishing</span></div>
    <div class="barcode-space"></div>
  </section>

  <section class="spine">
    <div class="spine-stack">
      <span class="gold-script spine-title">Quiet Harbor</span>
      <span class="subtitle"><em>Small Ceremonies For</em> <strong>The Restless Soul</strong></span>
      <span class="spine-publisher">Lantern Bough Publishing</span>
    </div>
  </section>

  <section class="front-cover">
    <div class="cover-art" role="img" aria-label="Watercolour illustration of a serene woman's profile crowned with vivid pink, violet and gold flower petals"></div>
    <p class="subtitle"><em>Small Ceremonies For</em> <strong>The Restless Soul</strong></p>
    <h1 class="front-title">
      <span class="gold-script line-one">Quiet</span>
      <span class="gold-script line-two">Harbor</span>
    </h1>
  </section>

</main>
</body>
</html>
```